Business Card Design

We are a commercial real estate brokerage in San Francisco, leasing office buildings downtown.
I would like a clean, elegant look. Simple but powerful .

Industry/Entity Type

Business

Contact Information for Business Card

Derek Holloway
lic# 07258143
415.555.0172
derek@velt-commercial.example
velt-commercial.example

```html
<!DOCTYPE html>
<html lang="en">
<head>
<meta charset="utf-8">
<title>Velt Commercial – Business Card</title>
<link rel="stylesheet" href="https://fonts.googleapis.com/css2?family=Jost:wght@500;600&family=Roboto+Condensed:wght@400&display=swap">
<style>
  :root {
    --slate: #7487a6;
    --ink: #272727;
    --paper: #ffffff;
    --backdrop: #ebe8e2;
    --row-text: #ffffff;
  }
  * { box-sizing: border-box; margin: 0; padding: 0; }
  html, body { width: 1200px; height: 1019px; overflow: hidden; background: var(--backdrop); }
  .canvas { position: relative; width: 1200px; height: 1019px; }
  .card {
    position: absolute; left: 355px; top: 92px;
    width: 490px; height: 834px;
    background: var(--paper);
    box-shadow: 0 6px 24px rgba(0,0,0,.18);
    overflow: hidden;
  }
  .card-header { position: relative; height: 466px; }
  .card-header svg { position: absolute; inset: 0; width: 100%; height: 100%; }
  .brand {
    position: absolute; left: 0; right: 0; top: 140px;
    display: flex; align-items: center; justify-content: center; gap: 18px;
  }
  .brand-mark { width: 56px; height: 56px; background: var(--slate); }
  .brand-name {
    font-family: "Jost", sans-serif; font-weight: 500;
    color: var(--slate); line-height: 1; text-transform: uppercase;
  }
  .brand-name .primary { display: block; font-size: 58px; letter-spacing: 1px; }
  .brand-name .secondary { display: block; font-size: 27px; letter-spacing: 1px; margin-top: 2px; }
  .holder-name {
    position: absolute; left: 0; right: 0; top: 284px; text-align: center;
    font-family: "Jost", sans-serif; font-weight: 600; font-size: 32px;
    letter-spacing: 1px; color: var(--slate); text-transform: uppercase;
  }
  .contact-list { list-style: none; }
  .contact-row {
    position: relative; height: 92px;
    display: flex; align-items: center;
    font-family: "Roboto Condensed", sans-serif; font-size: 20px; color: var(--row-text);
  }
  .contact-row.dark { background: var(--ink); }
  .contact-row.slate { background: var(--slate); }
  .contact-icon { position: absolute; left: 80px; width: 28px; height: 28px; }
  .contact-text { position: absolute; left: 148px; }
  .contact-arrow { position: absolute; right: 38px; width: 10px; height: 14px; }
</style>
</head>
<body>
<div class="canvas">
  <div class="card">
    <div class="card-header">
      <svg viewBox="0 0 245 233" preserveAspectRatio="none" aria-hidden="true">
        <polygon points="0,0 245,0 245,48 62,14" fill="var(--slate)"/>
        <polygon points="0,0 62,14 0,32" fill="var(--ink)"/>
        <polygon points="0,233 245,233 245,183 58,221" fill="var(--slate)"/>
        <polygon points="0,202 58,221 0,233" fill="var(--ink)"/>
      </svg>
      <div class="brand">
        <span class="brand-mark"></span>
        <span class="brand-name"><span class="primary">Velt</span><span class="secondary">Commercial</span></span>
      </div>
      <p class="holder-name">Derek Holloway</p>
    </div>
    <ul class="contact-list">
      <li class="contact-row dark">
        <span class="contact-text">lic# 07258143</span>
        <svg class="contact-arrow" viewBox="0 0 10 14"><polygon points="10,0 10,14 0,7" fill="#fff"/></svg>
      </li>
      <li class="contact-row slate">
        <svg class="contact-icon" viewBox="0 0 28 28"><rect x="8" y="2" width="12" height="24" rx="2" fill="none" stroke="var(--ink)" stroke-width="2"/><line x1="12" y1="22" x2="16" y2="22" stroke="var(--ink)" stroke-width="2"/></svg>
        <span class="contact-text">415.555.0172</span>
        <svg class="contact-arrow" viewBox="0 0 10 14"><polygon points="10,0 10,14 0,7" fill="#fff"/></svg>
      </li>
      <li class="contact-row dark">
        <svg class="contact-icon" viewBox="0 0 28 28"><rect x="3" y="7" width="22" height="15" fill="none" stroke="var(--slate)" stroke-width="2"/><polyline points="3,7 14,16 25,7" fill="none" stroke="var(--slate)" stroke-width="2"/></svg>
        <span class="contact-text">derek@velt-commercial.example</span>
        <svg class="contact-arrow" viewBox="0 0 10 14"><polygon points="10,0 10,14 0,7" fill="#fff"/></svg>
      </li>
      <li class="contact-row slate">
        <svg class="contact-icon" viewBox="0 0 28 28" fill="none" stroke="var(--ink)" stroke-width="1.8"><circle cx="14" cy="14" r="11"/><ellipse cx="14" cy="14" rx="5" ry="11"/><line x1="3" y1="14" x2="25" y2="14"/><line x1="5" y1="8" x2="23" y2="8"/><line x1="5" y1="20" x2="23" y2="20"/></svg>
        <span class="contact-text">velt-commercial.example</span>
        <svg class="contact-arrow" viewBox="0 0 10 14"><polygon points="10,0 10,14 0,7" fill="#fff"/></svg>
      </li>
    </ul>
  </div>
</div>
</body>
</html>
```